AGP letterhead

We need a letterhead design for our new company based in Los Angeles called "Amber Gate Pictures". We develop film and television projects. We work with investors, financiers, film production companies, film distribution and sales companies as well as studios. We would like to incorporate our logo (see attached) but make the letterhead simple and elegant. We need to include: logo, company address, phone number and company website.
Updates

Hello designers, Thanks for your submissions. For our letterhead, we are looking for something more simple and elegant. No heavy bars or lines. Make it feel light and clean. Not a lot of ink on the page. Use the logo and contact info but think "clean", "streamlined" and mostly white paper. Looking forward to seeing more... thanks! Amber Gate Pictures team

Target Market(s)

Studio executives, talent agents and agencies, financiers, investors.

Industry/Entity Type

It Company

Requirements
Must have
• Amber Gate Pictures logo (see attached). Logo may be cropped and altered appropriately for elegant letterhead design.
• Please include:
• COMPANY ADDRESS:
• Tolvane Arts Park
• 2850 Delmore Street
• Crest Hall, 2nd Floor
• Manhattan Beach, CA 90266
• COMPANY WEBSITE:
• www.ambergatepicturesco.example
• COMPANY PHONE NUMBER:
• 555-604-2187

```html
<!DOCTYPE html>
<html lang="en">
<head>
<meta charset="utf-8">
<title>Amber Gate Pictures – Letterhead</title>
<link rel="stylesheet" href="https://fonts.googleapis.com/css2?family=Dosis:wght@400;500;600&display=swap">
<style>
  :root {
    --backdrop: #e9e9e7;
    --paper: #ffffff;
    --teal-deep: #1d5569;
    --teal: #12738f;
    --teal-bright: #1f9cc4;
    --ink: #1d1d1f;
    --text: #3c4247;
    --text-soft: #7a8288;
    --rule: #dfe5e8;
    --mark: #3a3d42;
  }
  * { margin: 0; padding: 0; box-sizing: border-box; }
  html, body {
    width: 1063px;
    height: 1200px;
    overflow: hidden;
    background: var(--backdrop);
    font-family: "Dosis", sans-serif;
  }
  .letterhead {
    position: absolute;
    left: 92px;
    top: 30px;
    width: 880px;
    height: 1140px;
    background: var(--paper);
    box-shadow: 0 6px 22px rgba(0,0,0,0.18);
    overflow: hidden;
  }
  .accent-top, .accent-bottom {
    position: absolute;
    left: 0;
    width: 100%;
    display: block;
  }
  .accent-top { top: 0; height: 8px; }
  .accent-bottom { bottom: 0; height: 6px; }

  .brand {
    position: absolute;
    left: 58px;
    top: 30px;
    width: 160px;
    display: flex;
    flex-direction: column;
    align-items: center;
  }
  .brand-dot {
    width: 46px;
    height: 46px;
    border-radius: 50%;
    background: var(--mark);
  }
  .brand-name {
    margin-top: 8px;
    font-size: 13px;
    font-weight: 500;
    letter-spacing: 1.6px;
    text-transform: uppercase;
    color: var(--teal);
    white-space: nowrap;
  }
  .brand-tagline {
    margin-top: 3px;
    font-size: 6px;
    font-weight: 600;
    letter-spacing: 1px;
    text-transform: uppercase;
    color: var(--text-soft);
    white-space: nowrap;
  }

  .contact {
    position: absolute;
    right: 40px;
    top: 28px;
    width: 250px;
    list-style: none;
    color: var(--text);
    font-size: 13px;
    line-height: 16px;
  }
  .contact li {
    display: flex;
    align-items: flex-start;
    gap: 8px;
    margin-bottom: 3px;
  }
  .contact .icon {
    flex: 0 0 11px;
    width: 11px;
    height: 11px;
    margin-top: 3px;
    color: var(--teal);
  }

  .header-rule {
    position: absolute;
    left: 58px;
    right: 40px;
    top: 150px;
    height: 1px;
    background: var(--rule);
  }
</style>
</head>
<body>
  <main class="letterhead">
    <svg class="accent-top" viewBox="0 0 880 8" preserveAspectRatio="none" aria-hidden="true">
      <defs>
        <linearGradient id="tealFade" x1="0" y1="0" x2="1" y2="0">
          <stop offset="0" stop-color="#1d5569"/>
          <stop offset="1" stop-color="#0f7a96"/>
        </linearGradient>
      </defs>
      <rect x="0" y="0" width="880" height="8" fill="url(#tealFade)"/>
      <polygon points="545,0 880,0 880,8 520,8" fill="var(--ink)"/>
    </svg>

    <div class="brand">
      <span class="brand-dot"></span>
      <span class="brand-name">Amber Gate Pictures</span>
      <span class="brand-tagline">A Media Entertainment Company</span>
    </div>

    <ul class="contact">
      <li>
        <svg class="icon" viewBox="0 0 12 12" aria-hidden="true"><path d="M6 0.5a3.6 3.6 0 0 0-3.6 3.6C2.4 7 6 11.5 6 11.5S9.6 7 9.6 4.1A3.6 3.6 0 0 0 6 0.5zm0 5a1.4 1.4 0 1 1 0-2.8 1.4 1.4 0 0 1 0 2.8z" fill="currentColor"/></svg>
        <span>Tolvane Arts Park<br>2850 Delmore Street<br>Crest Hall, 2nd Floor<br>Manhattan Beach, CA 90266</span>
      </li>
      <li>
        <svg class="icon" viewBox="0 0 12 12" aria-hidden="true"><path d="M3 1h2l1 3-1.5 1a6 6 0 0 0 2.5 2.5L8 6l3 1v2a1.5 1.5 0 0 1-1.6 1.5A9 9 0 0 1 1.5 2.6 1.5 1.5 0 0 1 3 1z" fill="currentColor"/></svg>
        <span>555-604-2187</span>
      </li>
      <li>
        <svg class="icon" viewBox="0 0 12 12" aria-hidden="true"><rect x="0.8" y="2.2" width="10.4" height="7.6" rx="1" fill="none" stroke="currentColor" stroke-width="1.1"/><path d="M1 2.6 6 6.6 11 2.6" fill="none" stroke="currentColor" stroke-width="1.1"/></svg>
        <span>info@ambergatepicturesco.example</span>
      </li>
      <li>
        <svg class="icon" viewBox="0 0 12 12" aria-hidden="true"><circle cx="6" cy="6" r="5" fill="none" stroke="currentColor" stroke-width="1.1"/><ellipse cx="6" cy="6" rx="2.2" ry="5" fill="none" stroke="currentColor" stroke-width="1"/><line x1="1" y1="6" x2="11" y2="6" stroke="currentColor" stroke-width="1"/></svg>
        <span>www.ambergatepicturesco.example</span>
      </li>
    </ul>

    <div class="header-rule"></div>

    <svg class="accent-bottom" viewBox="0 0 880 6" preserveAspectRatio="none" aria-hidden="true">
      <defs>
        <linearGradient id="tealFoot" x1="0" y1="0" x2="1" y2="0">
          <stop offset="0" stop-color="#1d5569"/>
          <stop offset="1" stop-color="#0f7a96"/>
        </linearGradient>
      </defs>
      <rect x="0" y="0" width="880" height="6" fill="url(#tealFoot)"/>
      <polygon points="580,0 880,0 880,6 560,6" fill="var(--ink)"/>
    </svg>
  </main>
</body>
</html>
```